Meadowlight Soaps Business Card

The new business card design will incorporate my new logo components designed by one of your designers. Meadowlight Soaps creates high quality soaps and bath products. They would be suited for a Spa, Bed and Breakfast, Boutique environment. The look should be a white background.
Classy, soft and using the colour palet of the logo. The card will be two sided.

Reason: Need more time to make some changes and decide.

Target Market(s)

Looking to appeal to an upper end market. Spas, boutiques, independent gift stores, bridal salons, bed and breakfast, etc. I want the card to impart a sense of elegance, tranquility and Meadowlight. But also quality and value.

Industry/Entity Type

Business

Font styles to use
Sans Serif
Script

Requirements
Must have
• My logo on the front. But also on the back but faded out to allow written notes on the back.
On the front : Carol Pritchett
Owner/Creator
48 Fenwick Rd
Guelph, Ont N4K 2P9
519.402.6183
Creating Quality Handcrafted Soaps And Bath Products
Custom and Wholesale Orders Welcome
Www.meadowlightsoaps.ca
Www.facebook.com / MeadowlightSoapandBath
info@meadowlightsoaps.ca

```html
<!DOCTYPE html>
<html lang="en">
<head>
<meta charset="utf-8">
<title>Meadowlight Soaps – Business Card</title>
<link rel="stylesheet" href="https://fonts.googleapis.com/css2?family=Saira:wght@400;500;600&display=swap">
<style>
  :root {
    --page: #e9eaee;
    --card-white: #ffffff;
    --card-shade: #ececec;
    --sage: #86b3a8;
    --sage-deep: #6f9d92;
    --peach: #f2dccb;
    --ink: #2a2a2a;
    --on-sage: #ffffff;
  }
  * { box-sizing: border-box; margin: 0; padding: 0; }
  html, body {
    width: 1200px;
    height: 840px;
    overflow: hidden;
    background: var(--page);
    font-family: "Saira", sans-serif;
  }
  .card {
    position: absolute;
    left: 100px;
    top: 134px;
    width: 1000px;
    height: 572px;
    background: linear-gradient(160deg, var(--card-white) 30%, var(--card-shade) 100%);
    box-shadow: 0 10px 30px rgba(60, 70, 90, 0.18);
    overflow: hidden;
  }
  .card-waves {
    position: absolute;
    inset: 0;
    width: 100%;
    height: 100%;
  }
  .brand {
    position: absolute;
    left: 620px;
    top: 52px;
    width: 290px;
    text-align: center;
    color: var(--sage-deep);
  }
  .brand-dot {
    display: block;
    width: 64px;
    height: 64px;
    margin: 0 auto 14px;
    border-radius: 50%;
    background: var(--sage);
  }
  .brand-name {
    font-size: 30px;
    font-weight: 500;
    letter-spacing: 0.5px;
    line-height: 1.1;
  }
  .person {
    position: absolute;
    left: 600px;
    top: 196px;
    width: 330px;
    text-align: center;
    color: var(--ink);
  }
  .person-name {
    font-size: 30px;
    font-weight: 500;
    letter-spacing: 1.5px;
    line-height: 1.1;
  }
  .person-role {
    font-size: 20px;
    font-weight: 500;
    line-height: 1.3;
  }
  .address {
    position: absolute;
    right: 40px;
    top: 420px;
    text-align: right;
    color: var(--on-sage);
    font-size: 19px;
    line-height: 1.4;
    letter-spacing: 0.8px;
  }
  .contacts {
    position: absolute;
    left: 36px;
    top: 418px;
    list-style: none;
    color: var(--on-sage);
    font-size: 19px;
    letter-spacing: 1px;
  }
  .contacts li {
    display: flex;
    align-items: center;
    gap: 12px;
    height: 29px;
  }
  .contacts svg {
    width: 18px;
    height: 18px;
    flex: none;
    fill: none;
    stroke: var(--on-sage);
    stroke-width: 1.8;
  }
</style>
</head>
<body>
  <div class="card">
    <svg class="card-waves" viewBox="0 0 1000 572" preserveAspectRatio="none" aria-hidden="true">
      <path fill="var(--peach)" d="M0,382 C140,318 250,286 420,276 C560,268 640,296 740,276 C860,252 930,180 1000,116 L1000,140 C930,200 860,270 740,292 C640,312 560,284 420,292 C250,302 140,334 0,398 Z"/>
      <path fill="var(--sage)" d="M0,410 C150,336 260,304 420,300 C560,296 630,322 740,304 C860,284 930,226 1000,170 L1000,572 L0,572 Z"/>
      <path fill="var(--card-white)" opacity="0.85" d="M120,372 C240,322 340,304 470,306 C580,308 640,324 740,312 C640,334 560,318 470,320 C340,322 240,340 120,372 Z"/>
    </svg>

    <div class="brand">
      <span class="brand-dot"></span>
      <div class="brand-name">Meadowlight Soaps</div>
    </div>

    <div class="person">
      <div class="person-name">OWEN HARTLEY</div>
      <div class="person-role">Managing Director</div>
    </div>

    <div class="address">
      48 Fenwick Rd<br>
      Guelph, Ont N4K 2P9
    </div>

    <ul class="contacts">
      <li>
        <svg viewBox="0 0 24 24"><path d="M5 3h4l2 5-3 2a11 11 0 0 0 6 6l2-3 5 2v4a2 2 0 0 1-2 2A17 17 0 0 1 3 5a2 2 0 0 1 2-2z"/></svg>
        519.402.6183
      </li>
      <li>
        <svg viewBox="0 0 24 24"><rect x="6" y="2" width="12" height="20" rx="2"/><line x1="10" y1="18" x2="14" y2="18"/></svg>
        519.402.6184
      </li>
      <li>
        <svg viewBox="0 0 24 24"><rect x="3" y="9" width="18" height="12" rx="1"/><rect x="7" y="3" width="10" height="6"/><line x1="7" y1="14" x2="17" y2="14"/></svg>
        519.402.6185
      </li>
      <li>
        <svg viewBox="0 0 24 24"><rect x="2" y="5" width="20" height="14" rx="1"/><path d="M2 6l10 7 10-7"/></svg>
        info@meadowlightsoaps.ca
      </li>
      <li>
        <svg viewBox="0 0 24 24"><circle cx="12" cy="12" r="10"/><ellipse cx="12" cy="12" rx="4" ry="10"/><line x1="2" y1="12" x2="22" y2="12"/></svg>
        www.meadowlightsoaps.ca
      </li>
    </ul>
  </div>
</body>
</html>
```